Business card por a urban DJ, up scale audience target

Need a sober design, modern, conservative colors but i can consider some options, y play rnb, hip hop, EDM and top40.

Business card for contact and personal info, double sided, use logo attrached please; im 42 so i need a card acording to my age an target audience.

Target Market(s)

Adult people, up scale audience

Industry/Entity Type

Music Download

Contact Information for Business Card

Cel (318) 4207265518 www.lumadrift.com

Requirements
Must have
• open mind
Nice to have
• open mind
Should not have
• DJ

```html
<!DOCTYPE html>
<html lang="en">
<head>
<meta charset="utf-8">
<title>Lumadrift business card</title>
<link href="https://fonts.googleapis.com/css2?family=Open+Sans:wght@400;600;800&family=Exo+2:wght@500&display=swap" rel="stylesheet">
<style>
  :root {
    --bg: #3a3430;
    --card: #141414;
    --card-edge: #1c1c1c;
    --ink: #ffffff;
    --ink-soft: #d8d8d8;
    --rule: #8a8a8a;
  }
  * { margin: 0; padding: 0; box-sizing: border-box; }
  html, body { width: 1200px; height: 780px; overflow: hidden; }
  body {
    background: var(--bg);
    font-family: "Open Sans", Arial, sans-serif;
    color: var(--ink);
    position: relative;
  }
  .card {
    position: absolute;
    top: 240px;
    width: 525px;
    height: 300px;
    background: var(--card);
    border: 1px solid var(--card-edge);
    border-radius: 3px;
    box-shadow: 0 6px 18px rgba(0,0,0,0.45);
  }
  .card--front { left: 50px; }
  .card--back { left: 625px; }

  .brand-name {
    font-family: "Open Sans", Arial, sans-serif;
    font-weight: 800;
    color: var(--ink);
    letter-spacing: 2px;
    line-height: 1;
  }
  .card--front .brand-name {
    position: absolute;
    left: 0; right: 0; top: 50%;
    transform: translateY(-50%);
    text-align: center;
    font-size: 120px;
  }
  .card--back .brand-name {
    position: absolute;
    left: 34px; top: 34px;
    font-size: 64px;
  }
  .divider {
    position: absolute;
    left: 34px; right: 34px; top: 122px;
    height: 1px;
    background: var(--rule);
  }
  .contact-list {
    position: absolute;
    left: 34px; top: 138px;
    list-style: none;
    font-size: 14px;
    color: var(--ink-soft);
  }
  .contact-list li {
    display: flex;
    align-items: center;
    gap: 12px;
    height: 22px;
  }
  .contact-icon { width: 13px; height: 13px; flex: none; }
  .person {
    position: absolute;
    right: 34px; top: 160px;
    text-align: right;
  }
  .person-name {
    font-family: "Exo 2", "Open Sans", sans-serif;
    font-weight: 500;
    font-size: 19px;
    letter-spacing: 0.5px;
    padding-bottom: 3px;
    border-bottom: 1px solid var(--rule);
    padding-left: 40px;
  }
  .person-role {
    font-size: 13px;
    color: var(--ink-soft);
    margin-top: 2px;
  }
  .address {
    position: absolute;
    right: 34px; bottom: 30px;
    text-align: right;
    font-size: 16px;
    line-height: 1.3;
    color: var(--ink-soft);
  }
</style>
</head>
<body>
  <section class="card card--front">
    <div class="brand-name">LUMA</div>
  </section>

  <section class="card card--back">
    <div class="brand-name">LUMA</div>
    <div class="divider"></div>

    <ul class="contact-list">
      <li>
        <svg class="contact-icon" viewBox="0 0 13 13" aria-hidden="true">
          <rect width="13" height="13" rx="1.5" fill="#fff"/>
          <path d="M4 2.5 L5.5 4.5 L4.7 5.5 Q5.8 7.5 7.5 8.3 L8.5 7.5 L10.5 9 L9.5 10.5 Q5.5 10 2.5 3.5 Z" fill="#141414"/>
        </svg>
        <span>(318) 4207265518</span>
      </li>
      <li>
        <svg class="contact-icon" viewBox="0 0 13 13" aria-hidden="true">
          <rect width="13" height="13" rx="1.5" fill="#fff"/>
          <rect x="2.5" y="3.5" width="8" height="6" fill="none" stroke="#141414" stroke-width="1"/>
          <path d="M2.5 3.5 L6.5 7 L10.5 3.5" fill="none" stroke="#141414" stroke-width="1"/>
        </svg>
        <span>info@lumadrift.com</span>
      </li>
      <li>
        <svg class="contact-icon" viewBox="0 0 13 13" aria-hidden="true">
          <rect width="13" height="13" rx="1.5" fill="#fff"/>
          <circle cx="6.5" cy="6.5" r="4" fill="none" stroke="#141414" stroke-width="1"/>
          <ellipse cx="6.5" cy="6.5" rx="1.7" ry="4" fill="none" stroke="#141414" stroke-width="0.8"/>
          <line x1="2.5" y1="6.5" x2="10.5" y2="6.5" stroke="#141414" stroke-width="0.8"/>
        </svg>
        <span>www.lumadrift.com</span>
      </li>
    </ul>

    <div class="person">
      <div class="person-name">Owen Carrick</div>
      <div class="person-role">Director</div>
    </div>

    <address class="address" style="font-style: normal;">
      PO Box 4817<br>
      Marden Vale SA 5072
    </address>
  </section>
</body>
</html>
```